International business needs business cards

Our company, DRV Ventures Inc. is in the business of supplying a range construction products with particular emphasis on CEMENT. We have developed our own brand - TORVAN SUPPLIES - with which to infiltrate the market. We are launching our brand of cement (TORVAN Type IS Cement) into the Caribbean which is unlike anything this market has ever seen. A monopoly has existed here for the past 60-odd years and the market has now opened to allow the importation of other brands and consumers are anxious and ready for change/improvement. We are very excited to be launching and want to make a great first impression. We will be conducting workshops and seminars (from government level to the hardware store owners) and we want our business card to give us the strong, confident introduction that we need.

Target Market(s)

construction; builders; engineers; home owners

Industry/Entity Type

Construction

Contact Information for Business Card

Marisol Depree
CEO
cell # 1 555 4180736
Ground floor,Lindell Plaza Suite 2734
George Town,Grand Cayman
Cayman Islands,KY1-4823
EMAIL: m.depree@drvventuresinc.example
web site drvventuresinc.example

COMPANY: skype info drv.ventures.example

second card
Yvette Brannock-Depree
CFO
CELL# 1 555 607 3941
George Town,Grand Cayman
Cayman Islands,KY1-4823
EMAIL: y.brannockdepree@drvventuresinc.example
website drvventuresinc.example

Requirements
Must have
• Business cards must display BOTH logos - DRV is the company and TORVAN is the brand.

```html
<!DOCTYPE html>
<html lang="en">
<head>
<meta charset="utf-8">
<title>DRV Ventures Inc. – Business Card</title>
<link href="https://fonts.googleapis.com/css2?family=Open+Sans:wght@400;600;700&display=swap" rel="stylesheet">
<style>
  :root {
    --stage: #e9e7e4;
    --brand-red: #7d1b21;
    --brand-red-light: #9a2a30;
    --ink: #1b1b1b;
    --text-grey: #6b6b6b;
    --paper: #ffffff;
    --paper-shade: #ececec;
    --back-black: #0b0b0b;
    --back-sheen: #2a2a2a;
    --emblem-grey: #5a5a5a;
  }
  * { margin: 0; padding: 0; box-sizing: border-box; }
  html, body {
    width: 1200px;
    height: 843px;
    overflow: hidden;
    background: var(--stage);
    font-family: "Open Sans", Arial, sans-serif;
  }
  .sheet {
    position: relative;
    width: 1200px;
    height: 843px;
  }
  .card {
    position: absolute;
    left: 290px;
    width: 620px;
    height: 354px;
    overflow: hidden;
    box-shadow: 0 6px 18px rgba(0,0,0,0.18);
  }

  /* Front */
  .card-front {
    top: 52px;
    background: linear-gradient(160deg, var(--paper) 55%, var(--paper-shade) 100%);
  }
  .name-band {
    position: absolute;
    left: 0;
    top: 40px;
    width: 400px;
    height: 62px;
    background: linear-gradient(90deg, var(--brand-red) 0%, var(--brand-red-light) 100%);
    padding: 8px 0 0 28px;
    color: var(--paper);
  }
  .person-name {
    font-size: 21px;
    font-weight: 600;
    line-height: 1.2;
    letter-spacing: 0.2px;
  }
  .person-title {
    font-size: 12px;
    font-weight: 400;
    line-height: 1.4;
  }
  .company-mark {
    position: absolute;
    left: 362px;
    top: 58px;
    display: flex;
    align-items: flex-start;
    gap: 10px;
  }
  .company-square {
    width: 64px;
    height: 64px;
    background: var(--brand-red);
    flex: none;
  }
  .company-name {
    font-weight: 700;
    color: var(--ink);
    line-height: 0.95;
    margin-top: 2px;
  }
  .company-name .initials {
    display: block;
    font-size: 50px;
    letter-spacing: 1px;
  }
  .company-name .suffix {
    display: block;
    font-size: 13px;
    letter-spacing: 0.4px;
    margin-top: 4px;
  }
  .contact {
    position: absolute;
    left: 28px;
    top: 140px;
    font-size: 14px;
    line-height: 1.38;
    color: var(--text-grey);
    list-style: none;
  }
  .contact .label {
    color: var(--brand-red);
    font-weight: 700;
  }
  .contact .address { margin-top: 10px; }
  .brand-mark {
    position: absolute;
    left: 430px;
    top: 226px;
    display: flex;
    flex-direction: column;
    align-items: center;
    gap: 8px;
  }
  .brand-circle {
    width: 78px;
    height: 78px;
    border-radius: 50%;
    background: var(--emblem-grey);
  }
  .brand-name {
    font-size: 14px;
    font-weight: 700;
    letter-spacing: 1.5px;
    color: var(--emblem-grey);
  }

  /* Back */
  .card-back {
    top: 437px;
    background: linear-gradient(115deg, var(--back-black) 0%, var(--back-black) 40%, var(--back-sheen) 55%, var(--back-black) 70%);
  }
  .back-mark {
    position: absolute;
    left: 50%;
    top: 110px;
    transform: translateX(-50%);
    display: flex;
    align-items: center;
    gap: 14px;
  }
  .back-square {
    width: 78px;
    height: 78px;
    background: var(--brand-red);
  }
  .back-name {
    font-size: 40px;
    font-weight: 700;
    color: var(--paper);
    letter-spacing: 1px;
  }
  .back-web {
    position: absolute;
    left: 0;
    right: 0;
    top: 262px;
    text-align: center;
    font-size: 14px;
    letter-spacing: 2px;
    color: var(--paper);
  }
</style>
</head>
<body>
<main class="sheet">
  <section class="card card-front" aria-label="Business card front">
    <div class="name-band">
      <p class="person-name">Marisol Depree</p>
      <p class="person-title">CEO</p>
    </div>

    <div class="company-mark">
      <span class="company-square" aria-hidden="true"></span>
      <p class="company-name">
        <span class="initials">DRV</span>
        <span class="suffix">VENTURES INC.</span>
      </p>
    </div>

    <ul class="contact">
      <li><span class="label">Mobile:</span>1 555 4180736</li>
      <li>m.depree@drvventuresinc.example</li>
      <li>www.drvventuresinc.example</li>
      <li class="address">Ground floor</li>
      <li>Lindell Plaza Suite 2734</li>
      <li>George Town,Grand Cayman</li>
      <li>Cayman Islands,KY1-4823</li>
    </ul>

    <div class="brand-mark">
      <span class="brand-circle" aria-hidden="true"></span>
      <p class="brand-name">TORVAN</p>
    </div>
  </section>

  <section class="card card-back" aria-label="Business card back">
    <div class="back-mark">
      <span class="back-square" aria-hidden="true"></span>
      <p class="back-name">DRV</p>
    </div>
    <p class="back-web">www.drvventuresinc.example</p>
  </section>
</main>
</body>
</html>
```